Local fast-growing company in the service sector

We are looking for a modern business card design, which should also appear on our letterheads

Target Market(s)

Private and industrial sectors

Contact Information for Business Card

Vorname Name
Kellberger Str. 18
71409 Lindenfeld
Tel.: 07146-839214-0
Name@agentur-kvtl.de

Colors
9d9d9d
919191
aaaaaa

Requirements
Must have
• The logo (file) in silver

```html
<!DOCTYPE html>
<html lang="de">
<head>
<meta charset="utf-8">
<title>KVTL – Visitenkarte</title>
<link href="https://fonts.googleapis.com/css2?family=Open+Sans:wght@400;600&display=swap" rel="stylesheet">
<style>
  :root {
    --stage: #ecebe9;
    --card-dark: #58595b;
    --card-light: #a7a9ac;
    --silver: #9d9d9d;
    --silver-mid: #919191;
    --silver-light: #aaaaaa;
    --white: #ffffff;
  }
  * { box-sizing: border-box; margin: 0; padding: 0; }
  html, body {
    width: 1200px; height: 900px; overflow: hidden;
    background: var(--stage);
    font-family: "Open Sans", Arial, sans-serif;
  }
  .canvas { position: relative; width: 1200px; height: 900px; }

  .card { position: absolute; overflow: hidden; }

  /* Contact side */
  .card--contact {
    left: 78px; top: 35px; width: 588px; height: 363px;
    background: var(--card-dark);
    color: var(--white);
  }
  .card__band {
    position: absolute; top: 0; right: 0; width: 200px; height: 100%;
    background: var(--card-light);
  }
  .card__band-name {
    position: absolute; top: 50%; left: 50%;
    transform: translate(-50%, -50%);
    font-size: 52px; font-weight: 600; letter-spacing: 2px;
    color: var(--white);
  }
  .contact__name {
    position: absolute; left: 34px; top: 50px;
    font-size: 19px; font-weight: 400; letter-spacing: 0.3px;
  }
  .contact__address {
    position: absolute; left: 33px; top: 188px;
    font-size: 15.5px; line-height: 22px;
  }
  .contact__list {
    position: absolute; left: 33px; top: 249px;
    list-style: none; font-size: 15.5px; line-height: 22px;
  }
  .contact__list li { display: flex; align-items: center; gap: 6px; }
  .contact__icon { width: 14px; height: 14px; fill: var(--white); flex: none; }

  /* Brand side */
  .card--brand {
    left: 388px; top: 505px; width: 567px; height: 352px;
    background: var(--white);
  }
  .brand {
    position: absolute; left: 50%; top: 50%;
    transform: translate(-50%, -50%);
    display: flex; align-items: center; gap: 22px;
  }
  .brand__square {
    width: 80px; height: 80px; background: var(--silver-light);
  }
  .brand__text { display: flex; flex-direction: column; }
  .brand__name {
    font-size: 68px; font-weight: 600; line-height: 1;
    letter-spacing: 4px; color: var(--silver);
  }
  .brand__domain {
    font-size: 22px; font-weight: 400; line-height: 1.2;
    letter-spacing: 1.5px; color: var(--silver-mid);
  }
</style>
</head>
<body>
<main class="canvas">

  <section class="card card--contact" aria-label="Visitenkarte Vorderseite">
    <div class="card__band"><span class="card__band-name">KVTL</span></div>
    <p class="contact__name">VORNAME NAME</p>
    <p class="contact__address">Kellberger Str. 18<br>71409 Lindenfeld</p>
    <ul class="contact__list">
      <li>
        <svg class="contact__icon" viewBox="0 0 24 24" aria-hidden="true"><path d="M6.6 10.8a15.1 15.1 0 0 0 6.6 6.6l2.2-2.2c.3-.3.7-.4 1-.2 1.1.4 2.3.6 3.6.6.6 0 1 .4 1 1V20c0 .6-.4 1-1 1A17 17 0 0 1 3 4c0-.6.4-1 1-1h3.5c.6 0 1 .4 1 1 0 1.3.2 2.5.6 3.6.1.3 0 .7-.2 1z"/></svg>
        <span>07146-839214-0</span>
      </li>
      <li>
        <svg class="contact__icon" viewBox="0 0 24 24" aria-hidden="true"><path d="M2 5h20v14H2z M3.5 6.5 12 13l8.5-6.5" fill="none" stroke="#fff" stroke-width="2"/></svg>
        <span>Name@agentur-kvtl.de</span>
      </li>
      <li>
        <svg class="contact__icon" viewBox="0 0 24 24" aria-hidden="true"><circle cx="12" cy="12" r="10"/><path d="M2 12h20M12 2c3 3 3 17 0 20M12 2c-3 3-3 17 0 20" fill="none" stroke="#58595b" stroke-width="1.5"/></svg>
        <span>www.agentur-kvtl.de</span>
      </li>
    </ul>
  </section>

  <section class="card card--brand" aria-label="Visitenkarte Rückseite">
    <div class="brand">
      <span class="brand__square" aria-hidden="true"></span>
      <div class="brand__text">
        <span class="brand__name">KVTL</span>
        <span class="brand__domain">agentur-kvtl.de</span>
      </div>
    </div>
  </section>

</main>
</body>
</html>
```